Furniture Wholesaler PowerPoint Template Refresh

Harlow Provisions is a family owned and operated furniture wholesaler that works with retailers like Bramlet, Quorvex, and Tallyhold to sell multifunctional furniture and home décor pieces.

We are looking for a new company PowerPoint template, primarily to be used by our sales team when working with our new and existing retail partners. Our current slideshow deck is attached below. We would like the new design to have a more modern and minimalist feel with at least 3-4 slide design options.

Our current logo is also included in the old slideshow attached below, but we are not looking to emphasize it in the new PowerPoint design.

Target Market(s)

This presentation will be used by our sales team to inform existing and potential retail partners of our company history, product selections, and fulfillment capabilities.

Industry/Entity Type

Ecommerce

Font styles to use
Other font styles liked:
• Please use Windows system fonts for any text. Our logo font is Myriad Pro, which should only be used for any graphics.

Colors

Designer to choose colors to be used in the design.

Requirements
Must have
• - at least 3-4 slide design options
- redesign of the image on slide 4 in the old presentation (attached below)
- same slide layout options as the old presentation, including a cover slide, title with text slide, title with text and image slide, and title with image slide.
- Blue and white as main colors with red as the accent. RGB codes are:
Blue - R0, G67, B104
White - R255, G255, B255
Red - R181, G36, B25
Should not have
• - do not emphasize our logo in new design (especially the blue ball)

```html
<!DOCTYPE html>
<html lang="en">
<head>
<meta charset="utf-8">
<title>Harlow Provisions – Presentation Template</title>
<link rel="stylesheet" href="https://fonts.googleapis.com/css2?family=Anton&family=Arimo:ital,wght@0,400;0,700;1,400&display=swap">
<style>
  :root {
    --blue: rgb(0, 67, 104);
    --blue-deep: #00354f;
    --red: rgb(181, 36, 25);
    --white: #ffffff;
    --ink: #222222;
    --stage: #e6e5e4;
    --head: "Anton", Impact, sans-serif;
    --body: "Arimo", Arial, sans-serif;
  }
  * { box-sizing: border-box; margin: 0; padding: 0; }
  html, body { width: 888px; height: 1200px; overflow: hidden; }
  body {
    background: var(--stage);
    font-family: var(--body);
    display: flex;
    flex-direction: column;
    align-items: center;
    justify-content: center;
    gap: 24px;
  }
  .slide {
    position: relative;
    width: 496px;
    height: 372px;
    background: var(--white);
    overflow: hidden;
    box-shadow: 0 6px 14px rgba(0,0,0,0.22);
  }
  .photo { position: absolute; left: 0; width: 100%; }

  /* Cover */
  .cover .photo {
    top: 0; height: 234px;
    background: radial-gradient(circle at 80% 25%, #f3e9a4 0%, #b7c35d 25%, #5f7f2c 60%, #3b5520 100%);
  }
  .cover .photo::after {
    content: ""; position: absolute; left: 0; right: 0; bottom: 0; height: 6px; background: #f4eee4;
  }
  .cover .band {
    position: absolute; left: 0; right: 0; top: 234px; bottom: 0;
    background: linear-gradient(180deg, var(--blue) 0%, var(--blue-deep) 100%);
  }
  .brand {
    position: absolute; left: 0; right: 0; top: 252px;
    display: flex; justify-content: center; align-items: center; gap: 8px;
    font-family: var(--body); font-weight: 700; font-size: 16px;
    color: var(--white); letter-spacing: 1px; text-transform: uppercase;
  }
  .brand .dot { width: 10px; height: 10px; border-radius: 50%; background: var(--red); }
  .cover-title {
    position: absolute; left: 0; right: 0; top: 298px;
    text-align: center; font-family: var(--head); font-size: 30px;
    color: var(--white); letter-spacing: 0.3px; word-spacing: 4px;
  }
  .url-pill {
    position: absolute; left: 174px; top: 347px; width: 148px; height: 25px;
    background: var(--red); color: var(--white);
    display: flex; align-items: center; justify-content: center; gap: 6px;
    font-size: 8px; letter-spacing: 1.8px;
  }

  /* Section title */
  .section .photo {
    top: 0; height: 338px;
    background: linear-gradient(160deg, #5a5a5a 0%, #8c8c8c 40%, #3e3e3e 70%, #6b6b6b 100%);
  }
  .section .band {
    position: absolute; left: 0; right: 0; top: 122px; height: 107px;
    background: var(--blue);
    text-align: center; color: var(--white);
  }
  .section h1 {
    font-family: var(--head); font-weight: 400; font-size: 49px; line-height: 1;
    margin-top: 17px; letter-spacing: 0.5px;
  }
  .section .tagline { font-weight: 700; font-size: 12.5px; margin-top: 10px; }

  /* Footer */
  .footer-rule {
    position: absolute; left: 0; right: 22px; top: 351px; height: 3px;
    background: linear-gradient(90deg, var(--blue) 0 50%, var(--red) 50% 100%);
  }
  .page-num {
    position: absolute; left: 459px; top: 341px; width: 22px; height: 22px; border-radius: 50%;
    background: var(--red); color: var(--white); font-size: 9px; font-weight: 700;
    display: flex; align-items: center; justify-content: center;
  }
  .footer-url {
    position: absolute; left: 15px; top: 359px; font-size: 7.5px; letter-spacing: 1.8px; color: var(--ink);
  }

  /* Content */
  .content .header {
    position: absolute; left: 0; right: 0; top: 0; height: 60px; background: var(--blue);
    display: flex; align-items: center; padding: 0 18px 0 15px; color: var(--white);
  }
  .content .bar { width: 2px; height: 28px; background: var(--white); margin-right: 9px; }
  .content h2 { font-family: var(--head); font-weight: 400; font-size: 19px; letter-spacing: 0.2px; flex: 1; }
  .content .brand-small { font-weight: 700; font-size: 12px; text-transform: uppercase; letter-spacing: 0.5px; }
  .content .intro {
    position: absolute; left: 25px; right: 25px; top: 72px;
    text-align: center; font-size: 10.5px; line-height: 1.3; color: var(--ink);
  }
  .content .photo {
    top: 229px; height: 143px;
    background: linear-gradient(180deg, #ffffff 0%, #e9edf1 20%, #c9cfd4 45%, #b0733a 62%, #8b5225 100%);
  }
  .quote {
    position: absolute; top: 125px; width: 167px; height: 95px;
    background: var(--blue); color: var(--white); text-align: center;
    font-size: 9px; line-height: 1.25; padding: 24px 9px 0;
  }
  .quote .by { font-style: italic; margin-top: 6px; }
  .quote.vision { left: 68px; font-size: 9.6px; }
  .quote.mission { left: 260px; font-size: 8.4px; padding-top: 23px; }
  .quote-mark {
    position: absolute; top: 109px; width: 34px; height: 34px; border-radius: 50%;
    background: var(--red); border: 2px solid var(--white);
    display: flex; align-items: center; justify-content: center;
    color: var(--white); font-family: var(--head); font-size: 28px; line-height: 1; padding-top: 10px;
  }
</style>
</head>
<body>

  <section class="slide cover">
    <div class="photo" role="img" aria-label="Photo of a brass alarm clock beside stacks of coins with seedlings on a sunny green bokeh background"></div>
    <div class="band"></div>
    <div class="brand"><span class="dot"></span>Harlow Provisions</div>
    <p class="cover-title">GREAT PRODUCT &nbsp;-&nbsp; SUPERIOR SERVICE</p>
    <div class="url-pill">
      <svg width="12" height="12" viewBox="0 0 12 12" fill="none" stroke="#fff" stroke-width="0.9">
        <circle cx="6" cy="6" r="5"/><ellipse cx="6" cy="6" rx="2.2" ry="5"/><line x1="1" y1="6" x2="11" y2="6"/>
      </svg>
      www.webaddress.com
    </div>
  </section>

  <section class="slide section">
    <div class="photo" role="img" aria-label="Black and white photo of a laptop showing code on a desk with a coffee mug"></div>
    <div class="band">
      <h1>MAKING A DIFFERENCE</h1>
      <p class="tagline">Excellence in Product Design, Quality, Fulfillment &amp; Customer Service</p>
    </div>
    <div class="footer-rule"></div>
    <div class="page-num">2</div>
    <p class="footer-url">www.webaddress.com</p>
  </section>

  <section class="slide content">
    <div class="header">
      <span class="bar"></span>
      <h2>WE ARE FURNISHINGS INDUSTRY LEADER</h2>
      <span class="brand-small">Harlow Provisions</span>
    </div>
    <p class="intro">Since 1976 privately held best - in - class quality &amp; service direct - to - consumer leading supplier direct containers continuous growth &amp; improvement.</p>
    <div class="photo" role="img" aria-label="Photo of eyeglasses on a closed laptop next to a mouse on a wooden desk"></div>
    <div class="quote vision">
      We will be our customer’s supplier of choice, for lifestyle and home furnishing solutions.
      <p class="by">- Harlow Vision -</p>
    </div>
    <div class="quote mission">
      The Harlow team is dedicated to providing stylish furniture solutions for the home, while delivering extraordinary value to our customers
      <p class="by">- Harlow Mission ; Dana Whitlock, CEO -</p>
    </div>
    <div class="quote-mark" style="left:135px">&ldquo;</div>
    <div class="quote-mark" style="left:327px">&ldquo;</div>
    <div class="footer-rule"></div>
    <div class="page-num">3</div>
    <p class="footer-url">www.webaddress.com</p>
  </section>

</body>
</html>
```